Realty Group Needs Classy, Contemporary Letterhead Design

We need a letterhead design for a new realty company located in NY, USA. We buy investment properties to rehabilitate and or keep in our rental portfolio.

```html
<!DOCTYPE html>
<html lang="en">
<head>
<meta charset="utf-8">
<title>Meridian Realty Group – Letterhead</title>
<link rel="stylesheet" href="https://fonts.googleapis.com/css2?family=Arimo:wght@400;700&family=Poppins:wght@400;700&display=swap">
<style>
  :root {
    --backdrop: #c6c6c6;
    --paper: #ffffff;
    --header-tint: #ecebf1;
    --header-edge: #e1e0e8;
    --brand-purple: #4b2a8c;
    --ink: #1f1f1f;
    --muted: #8a8a92;
    --signature-tone: #d9d9de;
  }
  * { box-sizing: border-box; margin: 0; padding: 0; }
  html, body {
    width: 1200px; height: 1089px; overflow: hidden;
    background: var(--backdrop);
  }
  .letterhead {
    position: absolute; left: 246px; top: 30px;
    width: 708px; height: 1002px;
    background: var(--paper);
    box-shadow: 0 10px 30px rgba(0,0,0,0.18);
    overflow: hidden;
    font-family: "Arimo", Arial, sans-serif;
    color: var(--ink);
  }
  .header-band { position: absolute; left: 0; top: 0; width: 100%; height: 190px; }
  .brand {
    position: absolute; right: 52px; top: 70px; text-align: right;
    font-family: "Poppins", sans-serif; font-weight: 700; color: var(--brand-purple);
  }
  .brand-name { font-size: 36px; letter-spacing: -0.5px; line-height: 1; }
  .brand-sub { font-size: 13px; letter-spacing: 1px; line-height: 1.6; }
  .letter-body {
    position: absolute; left: 64px; top: 196px; width: 580px;
    font-size: 13px; line-height: 1.45;
  }
  .date { margin-bottom: 20px; }
  .recipient { margin-bottom: 20px; }
  .recipient strong { font-size: 14px; }
  .letter-body p { text-align: justify; margin-bottom: 12px; }
  .letter-body .para { text-indent: 24px; }
  .signature {
    width: 120px; height: 34px; margin: 10px 0 6px;
    background: linear-gradient(90deg, var(--signature-tone), transparent);
    border-radius: 4px;
  }
  .sender { font-weight: 700; font-size: 15px; }
  .contact {
    position: absolute; left: 270px; bottom: 46px;
    font-family: "Poppins", sans-serif; font-size: 12px; color: var(--muted);
    list-style: none; line-height: 1.75;
  }
  .contact li { display: flex; align-items: center; gap: 8px; }
  .contact svg { width: 11px; height: 11px; fill: var(--brand-purple); }
  .footer-bar {
    position: absolute; left: 0; bottom: 0; width: 100%; height: 12px;
    background: var(--brand-purple);
  }
</style>
</head>
<body>
  <main class="letterhead">
    <svg class="header-band" viewBox="0 0 708 190" preserveAspectRatio="none" aria-hidden="true">
      <defs>
        <linearGradient id="bandFill" x1="0" y1="0" x2="1" y2="0">
          <stop offset="0" stop-color="#f6f5f9"/>
          <stop offset="1" stop-color="var(--header-tint)"/>
        </linearGradient>
      </defs>
      <path d="M0 0 H708 V190 C480 170 240 120 0 40 Z" fill="url(#bandFill)"/>
    </svg>

    <div class="brand">
      <div class="brand-name">MERIDIAN</div>
      <div class="brand-sub">Realty Group, LLC</div>
    </div>

    <section class="letter-body">
      <div class="date">4th September 20XX</div>
      <div class="recipient">
        <strong>Ronny Reader</strong><br>
        CEO, Company Name<br>
        123 Address St<br>
        Anytown, ST 12345
      </div>
      <p>Dear Mr. Reader,<br>
      Lorem ipsum dolor sit amet, consectetuer adipiscing elit, sed diam nonummy nibh euismod tincidunt ut laoreet dolore magna aliquam erat volutpat. Ut wisi enim ad minim veniam, quis nostrud exerci tation ullamcorper suscipit lobortis nisl ut aliquip ex ea commodo consequat.</p>
      <p class="para">Duis autem vel eum iriure dolor in hendrerit in vulputate velit esse molestie consequat, vel illum dolore eu feugiat nulla facilisis at vero eros et accumsan.</p>
      <p class="para">Nam liber tempor cum soluta nobis eleifend option congue nihil imperdiet doming id quod mazim placerat facer possim assum. Typi non habent claritatem insitam; est usus legentis in iis qui facit eorum claritatem. Investigationes demonstraverunt lectores legere me lius quod ii legunt saepius.</p>
      <p>Sincerely,</p>
      <div class="signature" role="img" aria-label="Handwritten signature"></div>
      <div class="sender">Your Name</div>
    </section>

    <ul class="contact">
      <li><svg viewBox="0 0 24 24" aria-hidden="true"><path d="M6.6 10.8a15 15 0 0 0 6.6 6.6l2.2-2.2c.3-.3.7-.4 1-.2 1.1.4 2.3.6 3.6.6.6 0 1 .4 1 1V20c0 .6-.4 1-1 1C10.6 21 3 13.4 3 4c0-.6.4-1 1-1h3.5c.6 0 1 .4 1 1 0 1.3.2 2.5.6 3.6.1.3 0 .7-.2 1z"/></svg>(555) 014-2290</li>
      <li><svg viewBox="0 0 24 24" aria-hidden="true"><path d="M2 5h20v14H2z M2 5l10 8 10-8" /></svg>info@meridianrealtyllc.com</li>
      <li><svg viewBox="0 0 24 24" aria-hidden="true"><circle cx="12" cy="12" r="10"/></svg>www.meridianrealtyllc.com</li>
    </ul>

    <div class="footer-bar"></div>
  </main>
</body>
</html>
```